Etiketten für Imkerei mit Spezialisierung auf Bio Lagenhonig
Zielgruppe
wiesfalter.at - BioImkerei Lindorf
Kleine Nebenerwerbs Imkerei mit Spezialisierung auf Bio Lagenhonig (nähere Infos sind auf der Website nachzulesen)
Als weitere Produktlinie bieten wir Honig+ / Honig mit Zutaten wie Himbeer, Erdbeer, Haselnuss, Mohn, Ingwer, Thymian, usw an.
Zielgruppe: Personen die offen für die Vielfalt der Natur sind, gesunde und natürliche Lebensmittel lieben und die bereit sind die aufwändige, großteils manuelle, Arbeit entsprechend zu entlohnen.
Gesucht:
ÄNDERUNG: Da die Anforderung für das ausgesetzte Preisgeld offensichtlich zu komplex ist, reduziere ich die Anforderung auf Etiketten für die Produktserie Honig+, Gesamtkonzepte sind nicht erforderlich werden aber gerne angenommen.
ÜRSPRÜNGLICH:
Redesign der aktuellen Honigetiketten
Basisdesign für Lagenhonig und Honig+ das entsprechende Varianten zulässt.
Aufgabenstellung
Ich wünsche mir ein modernes, edles (oder Öko look) Design mit sehr guten Wiedererkennungswert das sich von gängigen Honigetiketten deutlich abhebt.
Das wiesfalter Logo soll enthalten sein kann aber bei Bedarf angepasst werden (z.B. monocrome Verison)
Für Lagenhonig werden derzeit 400g und 100g Gläser mit hohem schwarzen DrehKap Decke und,
für Honig+ 250g und 100g mit hohem silbenen DrehKap Deckel verwendet. Beispiele sind im Webshop unter https://solvenhof.at/index.php/wiesfalter ersichtilich.
Für das Ablaufdatum ist evtl. ein Feld für manuelle Stempelung vorzusehen.
Bitte die Sichtfeldregelung der EU Verpackungsverordnung einhalten.
Bisherige Etiketten hatten den Anspruch das diese auf guten Laserdruckern ausdruckbar waren - das ist jetzt nicht mehr zwingend notwendig (wäre für Kleinauflagen aber trotzdem vorteilhaft)

```html
<!DOCTYPE html>
<html lang="de">
<head>
<meta charset="utf-8">
<title>wiesfalter – Honig +</title>
<link href="https://fonts.googleapis.com/css2?family=Jost:wght@300;400&display=swap" rel="stylesheet">
<style>
  :root {
    --ink: #111111;
    --black: #000000;
    --paper: #ffffff;
    --honey: #f7a21b;
    --honey-soft: #fbd9a0;
    --honey-pale: #fdf1dc;
    --jar-amber: #e8860e;
    --jar-deep: #c4650a;
    --lid: #1c1c1c;
    --berry: #f0606a;
    --label-line: #d8d8d8;
  }
  * { box-sizing: border-box; margin: 0; padding: 0; }
  html, body {
    width: 1200px;
    height: 841px;
    overflow: hidden;
    background: var(--paper);
    font-family: "Jost", sans-serif;
    color: var(--ink);
  }
  .site-header {
    position: absolute;
    left: 0; top: 0;
    width: 1200px; height: 240px;
    background: var(--black);
    display: flex;
    align-items: center;
    justify-content: center;
  }
  .brand {
    display: flex;
    align-items: center;
    gap: 14px;
    color: var(--honey);
    font-weight: 400;
    font-size: 34px;
    letter-spacing: 0.12em;
  }
  .brand-dot {
    width: 18px; height: 18px;
    border-radius: 50%;
    background: var(--honey);
  }
  .main-nav {
    position: absolute;
    left: 0; top: 240px;
    width: 1200px; height: 81px;
  }
  .nav-band {
    position: absolute;
    inset: 0;
    background: linear-gradient(180deg, var(--honey-pale) 0%, #ffffff 50%, var(--honey-pale) 100%);
  }
  .nav-active-band {
    position: absolute;
    left: 700px; top: 0;
    width: 148px; height: 70px;
    background: var(--honey-soft);
  }
  .nav-link {
    position: absolute;
    top: 22px;
    font-size: 20px;
    font-weight: 300;
    letter-spacing: 0.32em;
    color: var(--ink);
    text-decoration: none;
  }
  .page-title {
    position: absolute;
    left: 168px; top: 356px;
    font-size: 31px;
    font-weight: 300;
    letter-spacing: 0.01em;
  }
  .product {
    position: absolute;
    top: 447px;
    width: 190px; height: 272px;
  }
  .product-jar {
    position: absolute;
    inset: 0;
    border-radius: 10px 10px 16px 16px;
    background:
      linear-gradient(180deg, var(--lid) 0 14%, #d9c7a6 14% 17%, var(--jar-amber) 17% 30%, var(--jar-deep) 30% 41%, var(--jar-amber) 77% 92%, #e4d8c6 92% 100%);
  }
  .jar-label {
    position: absolute;
    left: 0; top: 111px;
    width: 190px; height: 99px;
    background: var(--black);
  }
  .label-brand {
    position: absolute;
    left: 0; right: 0; top: 10px;
    text-align: center;
    font-size: 7px;
    font-weight: 400;
    letter-spacing: 0.12em;
    color: var(--honey);
  }
  .label-panel {
    position: absolute;
    left: 33px; top: 45px;
    width: 123px; height: 41px;
    border: 1px solid var(--label-line);
    color: #ffffff;
    font-size: 8px;
    font-weight: 300;
  }
  .panel-row {
    display: flex;
    height: 50%;
  }
  .panel-row + .panel-row { border-top: 1px solid var(--label-line); }
  .panel-cell {
    display: flex;
    align-items: center;
    padding-left: 3px;
    white-space: nowrap;
  }
  .panel-name { flex: 1; }
  .panel-flavour-field {
    width: 67px;
    background: var(--berry);
  }
  .panel-weight {
    width: 34px;
    border-right: 1px solid var(--label-line);
  }
  .panel-variety { flex: 1; }
</style>
</head>
<body>
  <header class="site-header">
    <div class="brand"><span class="brand-dot"></span>wiesfalter</div>
  </header>

  <nav class="main-nav">
    <div class="nav-band" role="img" aria-label="Wabenmuster in Honigorange als Hintergrund der Navigation"></div>
    <div class="nav-active-band"></div>
    <a class="nav-link" style="left:34px" href="#">start</a>
    <a class="nav-link" style="left:224px" href="#">jahreszeiten</a>
    <a class="nav-link" style="left:495px" href="#">lagen</a>
    <a class="nav-link" style="left:706px" href="#">produkte</a>
    <a class="nav-link" style="left:945px" href="#">kontakt</a>
  </nav>

  <h1 class="page-title">Honig +</h1>

  <div class="product" style="left:157px">
    <div class="product-jar" role="img" aria-label="Foto: Honigglas mit schwarzem Deckel"></div>
    <div class="jar-label">
      <div class="label-brand">wiesfalter</div>
      <div class="label-panel">
        <div class="panel-row">
          <div class="panel-cell panel-name">honig +</div>
          <div class="panel-flavour-field" role="img" aria-label="Wabenmuster in Erdbeerrot"></div>
        </div>
        <div class="panel-row">
          <div class="panel-cell panel-weight">100 g</div>
          <div class="panel-cell panel-variety">Erdbeere in Bio Honig</div>
        </div>
      </div>
    </div>
  </div>

  <div class="product" style="left:523px">
    <div class="product-jar" role="img" aria-label="Foto: Honigglas mit schwarzem Deckel"></div>
    <div class="jar-label">
      <div class="label-brand">wiesfalter</div>
      <div class="label-panel">
        <div class="panel-row">
          <div class="panel-cell panel-name">honig +</div>
          <div class="panel-flavour-field" role="img" aria-label="Wabenmuster in Erdbeerrot"></div>
        </div>
        <div class="panel-row">
          <div class="panel-cell panel-weight">100 g</div>
          <div class="panel-cell panel-variety">Erdbeere in Bio Honig</div>
        </div>
      </div>
    </div>
  </div>

  <div class="product" style="left:877px">
    <div class="product-jar" role="img" aria-label="Foto: Honigglas mit schwarzem Deckel"></div>
    <div class="jar-label">
      <div class="label-brand">wiesfalter</div>
      <div class="label-panel">
        <div class="panel-row">
          <div class="panel-cell panel-name">honig +</div>
          <div class="panel-flavour-field" role="img" aria-label="Wabenmuster in Erdbeerrot"></div>
        </div>
        <div class="panel-row">
          <div class="panel-cell panel-weight">100 g</div>
          <div class="panel-cell panel-variety">Erdbeere in Bio Honig</div>
        </div>
      </div>
    </div>
  </div>
</body>
</html>
```